VELO MARANTA - LUXURY RESORT ZEPHYR HOTEL

We wanna promote the luxury hotel based on marroquian stylish luxury decor, it is still a project but we need to expose it.
Houses will be A frame type houses surrounded by florest and water dumps - please check - odeleite amber lynx at google to check localisation
Container luxury houses also will be included heaven blue velvet and green and rose gold are the Color. The sky is the limit.

```html
<!DOCTYPE html>
<html lang="en">
<head>
<meta charset="utf-8">
<title>Velo Maranta — Stationery</title>
<link rel="stylesheet" href="https://fonts.googleapis.com/css2?family=Jost:wght@400&family=Source+Sans+3:wght@400;600&display=swap">
<style>
  :root {
    --backdrop: #a9a7a8;
    --paper: #f5f2f2;
    --tan: #c49a6c;
    --ink: #3c3b3b;
    --ink-soft: #4a4949;
    --white: #ffffff;
  }
  * { box-sizing: border-box; margin: 0; padding: 0; }
  html, body { width: 1200px; height: 770px; overflow: hidden; }
  body {
    background: var(--backdrop);
    position: relative;
    font-family: "Source Sans 3", sans-serif;
    color: var(--ink);
  }
  .sheet {
    position: absolute;
    background: var(--paper);
    box-shadow: 3px 4px 10px rgba(0,0,0,0.28);
  }
  .side-tab {
    position: absolute;
    left: 0;
    width: 10px;
    height: 70px;
    background: var(--tan);
  }
  .brand-name {
    position: absolute;
    font-family: "Source Sans 3", sans-serif;
    font-weight: 400;
    color: var(--tan);
    letter-spacing: 0.16em;
    white-space: nowrap;
  }

  /* Envelope front */
  .envelope-front { left: 61px; top: 203px; width: 560px; height: 254px; }
  .envelope-front .side-tab { top: 19px; width: 9px; }
  .envelope-front .brand-name { left: 34px; top: 39px; font-size: 15px; }
  .envelope-front .return-address {
    position: absolute; left: 34px; top: 62px;
    font-size: 8px; color: var(--ink-soft);
  }

  /* Envelope back */
  .envelope-back { left: 56px; top: 479px; width: 559px; height: 255px; }
  .envelope-back .flap { position: absolute; left: 0; top: 0; }

  /* Letterhead */
  .letterhead { left: 643px; top: 33px; width: 496px; height: 701px; }
  .letterhead .side-tab { top: 41px; width: 11px; }
  .letterhead .brand-name { left: 47px; top: 66px; font-size: 17px; }
  .contact-box {
    position: absolute; left: 284px; top: 41px; width: 212px; height: 70px;
    background: var(--tan);
    padding: 10px 50px 0 0;
    font-family: "Jost", sans-serif;
    font-size: 8.2px; line-height: 10.4px;
    color: var(--white);
    text-align: right;
  }
  .contact-line { display: flex; justify-content: flex-end; align-items: center; gap: 4px; white-space: nowrap; }
  .contact-line .icon { width: 6px; height: 6px; flex: none; }
  .contact-line.no-icon { padding-right: 10px; }

  .letter-date {
    position: absolute; left: 48px; top: 176px;
    font-size: 9.2px; font-weight: 600;
  }
  .recipient {
    position: absolute; left: 48px; top: 212px;
    font-size: 9.2px; font-weight: 600; line-height: 12px;
  }
  .letter-body {
    position: absolute; left: 47px; top: 282px; width: 401px;
    font-size: 7.4px; line-height: 12px; color: var(--ink-soft);
    text-align: justify; hyphens: auto;
  }
  .letter-body p + p { margin-top: 12px; }
  .signature {
    position: absolute; left: 356px; top: 526px; width: 78px; height: 36px;
    background: linear-gradient(90deg, rgba(40,40,40,0.08), rgba(40,40,40,0.16));
    border-radius: 4px;
  }
  .signer-title {
    position: absolute; left: 377px; top: 561px;
    font-size: 8px; color: var(--ink-soft); letter-spacing: 0.02em;
  }
</style>
</head>
<body>

  <section class="sheet envelope-front">
    <div class="side-tab"></div>
    <div class="brand-name">VELO MARANTA</div>
    <div class="return-address">Saltmere - Orvan Coast, Egypt</div>
  </section>

  <section class="sheet envelope-back">
    <svg class="flap" width="559" height="100" viewBox="0 0 559 100" aria-hidden="true">
      <path d="M0 0 H559 L547 68 Q541 93 514 93 H45 Q18 93 12 68 Z" fill="var(--tan)"/>
    </svg>
  </section>

  <section class="sheet letterhead">
    <div class="side-tab"></div>
    <div class="brand-name">VELO MARANTA</div>

    <div class="contact-box">
      <div class="contact-line no-icon">Saltmere - Orvan Coast, Egypt</div>
      <div class="contact-line">+20 1x xxxx xxxx
        <svg class="icon" viewBox="0 0 10 10" aria-hidden="true"><path d="M2 1 L4 1 L4.6 3.2 L3.4 4.2 Q4.6 6 6 6.6 L7 5.4 L9 6 L9 8 Q9 9 8 9 Q1 8 1 2 Q1 1 2 1 Z" fill="var(--white)"/></svg>
      </div>
      <div class="contact-line">Nadia.Halvorsen@marantastays.com
        <svg class="icon" viewBox="0 0 10 10" aria-hidden="true"><rect x="0.5" y="2" width="9" height="6.5" fill="var(--white)"/><path d="M0.5 2 L5 5.6 L9.5 2" fill="none" stroke="var(--tan)" stroke-width="0.9"/></svg>
      </div>
      <div class="contact-line">www.marantastays.com
        <svg class="icon" viewBox="0 0 10 10" aria-hidden="true"><g fill="none" stroke="var(--white)" stroke-width="0.8"><circle cx="5" cy="5" r="4.2"/><ellipse cx="5" cy="5" rx="1.8" ry="4.2"/><path d="M0.8 5 H9.2 M1.6 2.8 H8.4 M1.6 7.2 H8.4"/></g></svg>
      </div>
    </div>

    <div class="letter-date">Cartagena de Indias, Ocober 12,2015</div>

    <div class="recipient">
      Sr.<br>TOMAS VIDAL<br>Web Master<br>City
    </div>

    <div class="letter-body">
      <p>Contrary to popular belief, Lorem Ipsum is not simply random text. It has roots in a piece of classical Latin literature from 45 BC, making it over 2000 years old. Edwin Harrowgate, a Latin professor at Larkfield College in Virginia, looked up one of the more obscure Latin words, consectetur, from a Lorem Ipsum passage, and going through the cites of the word in classical literature,</p>
      <p>discovered the undoubtable source. Lorem Ipsum comes from sections 1.10.32 and 1.10.33 of "de Finibus Bonorum et Malorum" (The Extremes of Good and Evil) by Tullius Renn, written in 45 BC. This book is a treatise on the theory of ethics, very popular during the Renaissance. The first line of Lorem Ipsum, "Lorem ipsum dolor sit amet..", comes from a line in section 1.10.32.</p>
      <p>The standard chunk of Lorem Ipsum used since the 1500s is reproduced below for those interested. Sections 1.10.32 and 1.10.33 from "de Finibus Bonorum et Malorum" by Tullius Renn are also reproduced in their exact original form, accompanied by English versions from the 1914 translation by L. Ashdown.</p>
      <p>There are many variations of passages of Lorem Ipsum available, but the majority have suffered alteration in some form, by injected humour, or randomised words which don't look even slightly believable. If you are going to use a passage of Lorem Ipsum, you need to be sure there isn't anything embarrassing hidden in the middle of text. All the Lorem Ipsum generators o</p>
    </div>

    <div class="signature" role="img" aria-label="Handwritten signature of the founder"></div>
    <div class="signer-title">CEO/ FOUNDER</div>
  </section>

</body>
</html>
```